birchwell hollow cattle company website

we would like a home page, an about us page, a page for sires, a page for dams, A sale page where we can list progreny for sale and a contact us. on the about us page we would like there to be a family picture. on the sires page we would like to have a picture of each sire, a description beside them and a link to their online profile at northern hereford registry. on the dam page we would like to have a picture of each dam, aswell as a description beside them aswell as a link to the northern hereford registry site. would like the website to very mobile phone friendly as expecting most traffic to be on phone. we would like the website to look and feel very mich like a farm, rustic, barbed wire and other farm feels. we would also like a frozen genetics pages where we can include pictures and descriptions of the sires and dams aswell as a price for embryos and semen. we need to website to be easy to maintain so we can update pictures and information as it changes, we would like there to be a feature so that people can sign up to be on our mailing list by giving us their mailing addess and email and full name
aswell as an area where they can send us a message to contact us.

leaving for work for 3 weeks in the canadian arctic will have limited ability to use the internet

Target Market(s)

other ranchers, farmers, cattlemen,

Industry/Entity Type

farming, agriculture, cattle

Coding

Coded - Design and coding required

Requirements
Must have
• about page, contact page, sires page, dams page, SALE page.
Nice to have
• country/farm vibe, barbed wire, wood,

```html
<!DOCTYPE html>
<html lang="en">
<head>
<meta charset="utf-8">
<title>Birchwell Hollow Cattle Company</title>
<link href="https://fonts.googleapis.com/css2?family=Bebas+Neue&family=Great+Vibes&family=Poppins:wght@400;500;600&display=swap" rel="stylesheet">
<style>
:root{
  --brown:#4a2614;
  --brown-mid:#6b3a20;
  --cream:#faf1e2;
  --cream-light:#fdf8ef;
  --topbar:#f2e1c3;
  --ink:#1d1410;
  --text:#3b312b;
  --wood-dark:#2e2016;
  --wood:#4b3526;
  --footer:#1f1c1a;
  --rust:#9a5a3c;
  --white:#ffffff;
  --line:#e3dcd2;
}
*{margin:0;padding:0;box-sizing:border-box}
html,body{width:1200px;height:4605px;overflow:hidden}
body{font-family:"Poppins",sans-serif;color:var(--text);background:var(--cream);position:relative}
.display{font-family:"Bebas Neue",sans-serif;font-weight:400;letter-spacing:.5px;color:var(--ink)}
.script{font-family:"Great Vibes",cursive;color:var(--ink)}
section,header{position:absolute;left:0;width:1200px}
.abs{position:absolute}

.btn{display:inline-flex;align-items:center;gap:14px;background:var(--brown);color:var(--white);border-radius:30px;padding:0 5px 0 20px;height:44px;font-family:"Bebas Neue",sans-serif;font-size:15px;letter-spacing:1.2px;text-decoration:none}
.btn .arrow{width:34px;height:34px;border:2px solid var(--white);border-radius:50%;display:flex;align-items:center;justify-content:center}

.topbar{top:0;height:32px;background:var(--topbar);font-size:12px;color:var(--text)}
.topbar .socials{left:141px;top:9px;display:flex;gap:12px}
.topbar .socials span{width:13px;height:13px;border:1.5px solid var(--ink);border-radius:50%;display:block}
.topbar .contact-item{top:8px;display:flex;align-items:center;gap:6px;white-space:nowrap}

.site-header{top:32px;height:86px;background:var(--cream)}
.brand{left:141px;top:22px;font-family:"Bebas Neue",sans-serif;font-size:17px;line-height:17px;color:var(--ink);letter-spacing:.8px}
.nav{font-family:"Bebas Neue",sans-serif;font-size:15px;letter-spacing:.8px;color:var(--ink)}
.nav a{color:inherit;text-decoration:none;position:absolute;white-space:nowrap}
.header-cta{left:924px;top:20px}

.hero{top:118px;height:529px}
.hero-photo{position:absolute;inset:0;background:
  radial-gradient(ellipse 340px 300px at 1000px 300px,#8a3c1c 0%,#8a3c1c 40%,rgba(138,60,28,0) 100%),
  linear-gradient(180deg,#c7cbcb 0%,#b3b7b4 32%,#8f9270 50%,#7d8152 70%,#6f7046 100%)}
.hero-tag{left:141px;top:106px;background:var(--brown);color:var(--white);font-family:"Bebas Neue",sans-serif;font-size:12px;letter-spacing:1.4px;padding:3px 12px;border-radius:14px}
.hero-title{left:141px;top:135px;font-size:84px;line-height:80px;color:var(--ink)}
.hero-lead{left:141px;top:320px;width:420px;font-size:12.5px;line-height:20px;color:var(--ink)}
.hero-cta{left:141px;top:380px}

.stats{top:647px;height:122px;background:linear-gradient(90deg,var(--wood-dark),var(--wood) 25%,#3a281c 50%,var(--wood) 75%,var(--wood-dark))}
.stat{top:26px;color:var(--white)}
.stat .num{font-family:"Bebas Neue",sans-serif;font-size:58px;line-height:54px;color:var(--white)}
.stat .label{font-size:12.5px}

.main-body{top:769px;height:2258px;background:linear-gradient(180deg,var(--cream) 0,var(--cream) 1945px,var(--white) 1945px)}
.about-photo{left:141px;top:86px;width:417px;height:425px;border-radius:34px;background:linear-gradient(160deg,#6b4a33 0%,#8a6a4e 45%,#4d3a2c 100%)}
.badge{left:426px;top:340px;width:168px;height:157px;border-radius:16px;background:var(--brown);color:var(--white);text-align:center;padding-top:24px}
.badge .num{font-family:"Bebas Neue",sans-serif;font-size:58px;line-height:52px}
.badge .label{font-size:16px;line-height:22px}
.about-script{left:640px;top:80px;font-size:52px}
.about-title{left:642px;top:130px;font-size:50px}
.about-copy{left:642px;top:206px;width:420px;font-size:12.5px;line-height:23px;color:var(--ink)}
.about-copy p+p{margin-top:8px}
.about-cta{left:642px;top:426px}

.feature{top:572px;width:288px;height:232px;background:var(--white);border-radius:12px;box-shadow:0 4px 18px rgba(74,38,20,.08);text-align:center;padding-top:34px}
.feature .icon{width:76px;height:46px;margin:0 auto;background:var(--brown);border-radius:10px}
.feature h3{font-family:"Bebas Neue",sans-serif;font-weight:400;font-size:26px;color:var(--ink);margin-top:22px;letter-spacing:.4px}
.feature p{font-size:12.5px;line-height:23px;color:var(--ink);margin:8px 22px 0}

.tradition-script{left:0;width:1200px;text-align:center;top:866px;font-size:50px}
.tradition-title{left:0;width:1200px;text-align:center;top:918px;font-size:46px}
.tradition-rule{left:516px;top:978px}

.row{left:141px;width:917px;height:365px;border-radius:10px;background:linear-gradient(135deg,#f1eee9 0%,#e4e0da 50%,#f2efea 100%);box-shadow:0 4px 16px rgba(0,0,0,.1);overflow:hidden}
.row .photo{position:absolute;top:0;width:494px;height:365px}
.row .copy{position:absolute;top:48px;width:340px}
.row h2{font-family:"Bebas Neue",sans-serif;font-weight:400;font-size:50px;line-height:50px;color:var(--ink)}
.row p{font-size:12.5px;line-height:23px;color:var(--ink);margin-top:16px}
.row .btn{margin-top:24px}

.landscape{top:3027px;height:286px;background:linear-gradient(180deg,#e6c98a 0%,#c9a560 30%,#8f8a45 60%,#5f6a2e 100%)}

.contact{top:3313px;height:621px;background:var(--cream-light)}
.contact-script{left:0;width:1200px;text-align:center;top:70px;font-size:52px}
.contact-title{left:0;width:1200px;text-align:center;top:128px;font-size:48px}
.field{height:50px;background:var(--white);border:1px solid var(--line);display:flex;align-items:center;font-size:12px;color:#8a827a}
.field .ico{width:44px;display:flex;justify-content:center;border-right:1px solid var(--line);margin-right:12px;height:20px;align-items:center}
.field.tall{height:107px;align-items:flex-start;padding-top:15px}
.submit{left:293px;top:479px;width:614px;height:52px;background:var(--brown);color:var(--white);font-size:12px;font-weight:600;display:flex;align-items:center;justify-content:center;letter-spacing:.3px}

.signup{top:3934px;height:286px;background:linear-gradient(90deg,#2a1c13,#4a3324 30%,#3b2a1d 55%,#4d3526 80%,#2a1c13)}
.signup-script{left:0;width:1200px;text-align:center;top:44px;font-size:48px;color:var(--white)}
.signup-title{left:0;width:1200px;text-align:center;top:92px;font-size:46px;color:var(--white)}
.signup-rule{left:516px;top:146px}
.signup .field{top:169px;height:52px;border-radius:3px;border:none}
.signup-btn{left:926px;top:169px;width:120px;height:52px;background:var(--rust);color:var(--white);font-family:"Bebas Neue",sans-serif;font-size:22px;letter-spacing:1.5px;display:flex;align-items:center;justify-content:center;border-radius:3px}

.footer{top:4220px;height:385px;background:var(--footer);color:#e8e2da;font-size:12.5px}
.footer-brand{left:141px;top:140px;font-family:"Bebas Neue",sans-serif;font-size:30px;line-height:30px;color:var(--white);letter-spacing:1px}
.footer-brand .sub{font-size:18px;line-height:20px;letter-spacing:3px}
.footer-about{left:141px;top:212px;width:225px;font-size:11.5px;line-height:19px}
.footer h4{font-family:"Bebas Neue",sans-serif;font-weight:400;font-size:18px;color:var(--white);letter-spacing:.5px;margin-bottom:10px}
.footer ul{list-style:none}
.footer li{line-height:27px}
.contact-line{display:flex;gap:8px;line-height:20px;margin-bottom:8px}
.social li{display:flex;align-items:center;gap:10px;line-height:20px;margin-bottom:21px}
.social .dot{width:28px;height:28px;border:1.5px solid var(--white);border-radius:50%}
.copyright{left:0;width:1200px;text-align:center;top:352px;font-size:11.5px}
</style>
</head>
<body>

<div class="topbar abs" style="left:0;width:1200px">
  <div class="socials abs"><span></span><span></span><span></span><span></span></div>
  <div class="contact-item abs" style="left:663px">
    <svg width="13" height="10" viewBox="0 0 13 10"><rect x=".5" y=".5" width="12" height="9" fill="none" stroke="#1d1410"/><path d="M.5 .5 6.5 5.5 12.5 .5" fill="none" stroke="#1d1410"/></svg>
    Email: info@birchwellhollow.com
  </div>
  <div class="contact-item abs" style="left:901px">
    <svg width="12" height="12" viewBox="0 0 24 24"><path d="M6.6 10.8a15.1 15.1 0 0 0 6.6 6.6l2.2-2.2c.3-.3.7-.4 1-.2 1.1.4 2.3.6 3.6.6.6 0 1 .4 1 1V20c0 .6-.4 1-1 1A17 17 0 0 1 3 4c0-.6.4-1 1-1h3.5c.6 0 1 .4 1 1 0 1.3.2 2.5.6 3.6.1.3 0 .7-.2 1z" fill="#1d1410"/></svg>
    Phone: 403-555-0147
  </div>
</div>

<header class="site-header">
  <div class="brand abs">BIRCHWELL HOLLOW<br>CATTLE COMPANY</div>
  <nav class="nav abs" style="left:0;top:33px">
    <a style="left:472px">HOME</a>
    <a style="left:529px">ABOUT US</a>
    <a style="left:608px">SIRES</a>
    <a style="left:667px">DAMS</a>
    <a style="left:724px">FROZEN GENETICS</a>
    <a style="left:846px">FOR SALE</a>
  </nav>
  <a class="btn header-cta abs">CONTACT US <span class="arrow"><svg width="16" height="12" viewBox="0 0 16 12"><path d="M1 6h13M9 1l5 5-5 5" fill="none" stroke="#fff" stroke-width="2"/></svg></span></a>
</header>

<section class="hero">
  <div class="hero-photo" role="img" aria-label="Red Angus cattle standing in an open pasture under a cloudy sky"></div>
  <div class="hero-tag abs">CATTLE · LAND · LEGACY</div>
  <h1 class="hero-title display abs">HERITAGE<br>ANGUS RANCH</h1>
  <p class="hero-lead abs">We Raise Registered Angus Cattle, Preserve Working Lands, And Offer Frozen Genetics From Our Top Sires &amp; Dams.</p>
  <a class="btn hero-cta abs">CONTACT US <span class="arrow"><svg width="16" height="12" viewBox="0 0 16 12"><path d="M1 6h13M9 1l5 5-5 5" fill="none" stroke="#fff" stroke-width="2"/></svg></span></a>
</section>

<section class="stats">
  <div class="stat abs" style="left:141px"><div class="num">70+</div><div class="label">Years of Excellence</div></div>
  <div class="stat abs" style="left:438px"><div class="num">200+</div><div class="label">Herd of Cattle</div></div>
  <div class="stat abs" style="left:704px"><div class="num">50+</div><div class="label">Registered Sires</div></div>
  <div class="stat abs" style="left:982px"><div class="num">03</div><div class="label">Generations</div></div>
</section>

<section class="main-body">
  <div class="about-photo abs" role="img" aria-label="Ranch family of four with their dog in front of a weathered wooden barn"></div>
  <div class="badge abs"><div class="num">75+</div><div class="label">YEARS OF<br>EXPERIENCE</div></div>
  <div class="about-script script abs">About</div>
  <h2 class="about-title display abs">BIRCHWELL HOLLOW</h2>
  <div class="about-copy abs">
    <p>Nestled in the heart of cattle country, our family has dedicated over 70 years to raising exceptional Black Angus cattle. We pride ourselves on superior genetics, sustainable ranching practices, and the honest, hard-working values that have defined our operation for generations.</p>
    <p>In the rolling hills of Kentucky, we’ve spent four decades perfecting the Angus breed. Every animal is raised with integrity, pasture-to-pedigree. We invite you to explore our program.</p>
  </div>
  <a class="btn about-cta abs">READ MORE <span class="arrow"><svg width="16" height="12" viewBox="0 0 16 12"><path d="M1 6h13M9 1l5 5-5 5" fill="none" stroke="#fff" stroke-width="2"/></svg></span></a>

  <div class="feature abs" style="left:141px">
    <div class="icon" role="img" aria-label="Bull and calf icon"></div>
    <h3>SUPERIOR GENETICS</h3>
    <p>Our breeding program focuses on proven bloodlines that deliver consistent quality and performance.</p>
  </div>
  <div class="feature abs" style="left:456px">
    <div class="icon" role="img" aria-label="Cow icon"></div>
    <h3>REGISTERED ANGUS</h3>
    <p>All our cattle are registered with the Northern Hereford Registry with complete documentation.</p>
  </div>
  <div class="feature abs" style="left:769px">
    <div class="icon" role="img" aria-label="Family group icon"></div>
    <h3>FAMILY VALUES</h3>
    <p>Three generations of experience and dedication to ethical, sustainable cattle ranching.</p>
  </div>

  <div class="tradition-script script abs">Birchwell Hollow</div>
  <h2 class="tradition-title display abs">TRADITION &amp; QUALITY SINCE 1987</h2>
  <svg class="tradition-rule abs" width="168" height="8" viewBox="0 0 168 8"><path d="M2 6 Q84 0 166 3" fill="none" stroke="#1d1410" stroke-width="3" stroke-linecap="round"/></svg>

  <article class="row abs" style="top:1019px">
    <div class="copy" style="left:36px">
      <h2>HERD SIRES</h2>
      <p>Elite genetics with proven marbling &amp; calving ease. Semen available. Lorem Ipsum is simply dummy text of the printing and typesetting industry. Lorem Ipsum has been the industry's standard dummy text ever since the 1500s, when an unknown printer took a galley of type and scrambled it to make</p>
      <a class="btn">READ MORE <span class="arrow"><svg width="16" height="12" viewBox="0 0 16 12"><path d="M1 6h13M9 1l5 5-5 5" fill="none" stroke="#fff" stroke-width="2"/></svg></span></a>
    </div>
    <div class="photo" style="left:423px;border-top-left-radius:90px;background:linear-gradient(180deg,#b9c0c4 0%,#8d8f8a 40%,#6a3a22 62%,#b89a6a 85%,#c9ad7c 100%)" role="img" aria-label="Red Angus herd sire standing on straw inside steel pens"></div>
  </article>

  <article class="row abs" style="top:1427px">
    <div class="photo" style="left:0;border-top-right-radius:90px;background:linear-gradient(170deg,#c7b47a 0%,#9c8a52 40%,#e9e3d2 62%,#7a4c2a 100%)" role="img" aria-label="Milk can and glass bottles of fresh milk on a wooden table with a cow in the field behind"></div>
    <div class="copy" style="left:544px">
      <h2>FOUNDATION DAMS</h2>
      <p>Deep-pedigreed females with superior milk, fertility &amp; structure. Lorem Ipsum is simply dummy text of the printing and typesetting industry. Lorem Ipsum has been the industry's standard dummy text ever since the 1500s, when an unknown printer took a galley of type and scrambled it to make</p>
      <a class="btn">READ MORE <span class="arrow"><svg width="16" height="12" viewBox="0 0 16 12"><path d="M1 6h13M9 1l5 5-5 5" fill="none" stroke="#fff" stroke-width="2"/></svg></span></a>
    </div>
  </article>

  <article class="row abs" style="top:1833px">
    <div class="copy" style="left:36px">
      <h2>FROZEN GENETICS</h2>
      <p>Semen, embryos, and custom collections — shipped worldwide. Lorem Ipsum is simply dummy text of the printing and typesetting industry. Lorem Ipsum has been the industry's standard dummy text ever since the 1500s, when an unknown printer took a galley of type and scrambled it to make</p>
      <a class="btn">READ MORE <span class="arrow"><svg width="16" height="12" viewBox="0 0 16 12"><path d="M1 6h13M9 1l5 5-5 5" fill="none" stroke="#fff" stroke-width="2"/></svg></span></a>
    </div>
    <div class="photo" style="left:423px;border-top-left-radius:90px;background:linear-gradient(135deg,#8fb6c9 0%,#cfd3d4 40%,#a8a49c 65%,#5a6066 100%)" role="img" aria-label="Technician handling a liquid nitrogen tank for storing frozen semen straws"></div>
  </article>
</section>

<section class="landscape" role="img" aria-label="Dirt ranch road beside a barbed wire fence with cattle grazing at golden hour"></section>

<section class="contact">
  <div class="contact-script script abs">Get In Touch</div>
  <h2 class="contact-title display abs">INQUIRY, NOW</h2>
  <div class="field abs" style="left:293px;top:215px;width:299px"><span class="ico"><svg width="13" height="13" viewBox="0 0 14 14"><circle cx="7" cy="4" r="3" fill="none" stroke="#9a928a"/><path d="M1 13c0-3 3-5 6-5s6 2 6 5" fill="none" stroke="#9a928a"/></svg></span>First Name</div>
  <div class="field abs" style="left:608px;top:215px;width:299px"><span class="ico"><svg width="13" height="13" viewBox="0 0 14 14"><circle cx="7" cy="4" r="3" fill="none" stroke="#9a928a"/><path d="M1 13c0-3 3-5 6-5s6 2 6 5" fill="none" stroke="#9a928a"/></svg></span>Last Name</div>
  <div class="field abs" style="left:293px;top:283px;width:299px"><span class="ico"><svg width="14" height="10" viewBox="0 0 14 10"><rect x=".5" y=".5" width="13" height="9" fill="none" stroke="#9a928a"/><path d="M.5 .5 7 5.5 13.5 .5" fill="none" stroke="#9a928a"/></svg></span>Your Email</div>
  <div class="field abs" style="left:608px;top:283px;width:299px"><span class="ico"><svg width="13" height="13" viewBox="0 0 24 24"><path d="M6.6 10.8a15.1 15.1 0 0 0 6.6 6.6l2.2-2.2c.3-.3.7-.4 1-.2 1.1.4 2.3.6 3.6.6.6 0 1 .4 1 1V20c0 .6-.4 1-1 1A17 17 0 0 1 3 4c0-.6.4-1 1-1h3.5c.6 0 1 .4 1 1 0 1.3.2 2.5.6 3.6.1.3 0 .7-.2 1z" fill="none" stroke="#9a928a" stroke-width="1.6"/></svg></span>Phone</div>
  <div class="field tall abs" style="left:293px;top:349px;width:614px"><span class="ico"><svg width="13" height="13" viewBox="0 0 14 14"><circle cx="7" cy="7" r="6" fill="none" stroke="#9a928a"/><circle cx="7" cy="7" r="1.2" fill="#9a928a"/></svg></span>Ranch Inquiry, Cattle, Property...</div>
  <div class="submit abs">SUBMIT NOW</div>
</section>

<section class="signup">
  <div class="signup-script script abs">Sign Up</div>
  <h2 class="signup-title display abs">JOIN THE TRAIL LIST</h2>
  <svg class="signup-rule abs" width="168" height="8" viewBox="0 0 168 8"><path d="M2 6 Q84 0 166 3" fill="none" stroke="#fff" stroke-width="3" stroke-linecap="round"/></svg>
  <div class="field abs" style="left:154px;width:243px"><span class="ico"><svg width="13" height="13" viewBox="0 0 14 14"><circle cx="7" cy="4" r="3" fill="none" stroke="#9a928a"/><path d="M1 13c0-3 3-5 6-5s6 2 6 5" fill="none" stroke="#9a928a"/></svg></span>Full Name</div>
  <div class="field abs" style="left:411px;width:243px"><span class="ico"><svg width="14" height="10" viewBox="0 0 14 10"><rect x=".5" y=".5" width="13" height="9" fill="none" stroke="#9a928a"/><path d="M.5 .5 7 5.5 13.5 .5" fill="none" stroke="#9a928a"/></svg></span>Your Email</div>
  <div class="field abs" style="left:669px;width:243px"><span class="ico"><svg width="12" height="15" viewBox="0 0 12 15"><path d="M6 14S1 8.5 1 5.5a5 5 0 0 1 10 0C11 8.5 6 14 6 14z" fill="none" stroke="#9a928a"/><circle cx="6" cy="5.5" r="1.6" fill="#9a928a"/></svg></span>Street, City, Zip</div>
  <div class="signup-btn abs">SIGN UP</div>
</section>

<footer class="footer abs" style="left:0;width:1200px">
  <div class="footer-brand abs">BIRCHWELL HOLLOW<br><span class="sub">CATTLE COMPANY</span></div>
  <p class="footer-about abs">Nestled in the rolling hills of Kentucky, we’ve spent four decades perfecting the Angus breed.</p>
  <div class="abs" style="left:456px;top:62px">
    <h4>QUICK LINKS</h4>
    <ul><li>Home</li><li>About Us</li><li>Sires</li><li>Dams</li><li>Frozen Genetics</li><li>For Sale</li><li>Contact Us</li></ul>
  </div>
  <div class="abs" style="left:665px;top:62px;width:230px">
    <h4>CONTACT DETAILS</h4>
    <div class="contact-line"><svg width="12" height="15" viewBox="0 0 12 15" style="flex:none;margin-top:3px"><path d="M6 14S1 8.5 1 5.5a5 5 0 0 1 10 0C11 8.5 6 14 6 14z" fill="#fff"/><circle cx="6" cy="5.5" r="1.6" fill="#1f1c1a"/></svg><span>1248 Fence Line Rd.<br>Hollow Creek, AR 12345</span></div>
    <div class="contact-line"><svg width="12" height="12" viewBox="0 0 24 24" style="flex:none;margin-top:4px"><path d="M6.6 10.8a15.1 15.1 0 0 0 6.6 6.6l2.2-2.2c.3-.3.7-.4 1-.2 1.1.4 2.3.6 3.6.6.6 0 1 .4 1 1V20c0 .6-.4 1-1 1A17 17 0 0 1 3 4c0-.6.4-1 1-1h3.5c.6 0 1 .4 1 1 0 1.3.2 2.5.6 3.6.1.3 0 .7-.2 1z" fill="#fff"/></svg><span>Phone:<br>403-555-0147</span></div>
    <div class="contact-line"><svg width="13" height="10" viewBox="0 0 13 10" style="flex:none;margin-top:5px"><rect x=".5" y=".5" width="12" height="9" fill="#fff"/><path d="M.5 .5 6.5 5.5 12.5 .5" fill="none" stroke="#1f1c1a"/></svg><span>Email<br>Info@BirchwellHollow.com</span></div>
  </div>
  <div class="abs" style="left:957px;top:62px">
    <h4>SOCIAL MEDIA</h4>
    <ul class="social">
      <li><span class="dot"></span>Ranchbook</li>
      <li><span class="dot"></span>Barnreel</li>
      <li><span class="dot"></span>Fieldlink</li>
      <li><span class="dot"></span>Pasturegram</li>
    </ul>
  </div>
  <p class="copyright abs">© 2026 Birchwell Hollow. All Rights Reserved.</p>
</footer>

</body>
</html>
```